Looking for a modern, Professional business card design

We have a simple business card, but are looking for a more modern, professional look. A sample of the basic card is attached as well as the logo. We would also like to add that we offer:
Struggling with your finances?
- Learn to become debt free
- Discover the power of cash
- Control your money instead of it controlling you
Let us help you achieve a new level of financial freedom!
Also, we would like to have a "SPECIAL OFFER!: FREE 30 minute consultation"
Financial Planning

```html
<!DOCTYPE html>
<html lang="en">
<head>
<meta charset="utf-8">
<title>Clearpath Money Coaching – Business Card</title>
<link rel="stylesheet" href="https://fonts.googleapis.com/css2?family=Open+Sans:ital,wght@0,400;0,600;0,700;1,400;1,700&display=swap">
<style>
  :root {
    --backdrop: #3d3d3d;
    --card: #ffffff;
    --green-deep: #3a9a3e;
    --green-bright: #7dbb2f;
    --green-soft: #9ccf45;
    --green-wash: rgba(125, 187, 47, 0.32);
    --ink: #1c1c1c;
    --ink-soft: #4a4a4a;
    --ink-muted: #6b6b6b;
  }
  * { margin: 0; padding: 0; box-sizing: border-box; }
  html, body {
    width: 1105px; height: 1200px; overflow: hidden;
    background: var(--backdrop);
    font-family: "Open Sans", Arial, sans-serif;
  }
  .card {
    position: absolute; left: 193px;
    width: 718px; height: 412px;
    background: var(--card);
    overflow: hidden;
  }
  .card--front { top: 181px; }
  .card--back  { top: 637px; }

  /* front */
  .front__band {
    position: absolute; left: 0; top: 0;
    width: 330px; height: 100%;
    background: linear-gradient(100deg, var(--green-wash) 0%, rgba(156, 207, 69, 0.12) 55%, rgba(255, 255, 255, 0) 100%);
  }
  .front__mark {
    position: absolute; left: 18px; top: 82px;
    width: 84px; height: 84px; border-radius: 50%;
    background: radial-gradient(circle at 35% 35%, var(--green-soft), var(--green-bright));
  }
  .front__accent {
    position: absolute; right: 0; top: 54px;
    width: 14px; height: 51px;
    background: linear-gradient(90deg, var(--green-deep), var(--green-soft));
  }
  .front__details {
    position: absolute; right: 38px; top: 50px;
    text-align: right;
  }
  .person__name {
    font-size: 25px; font-weight: 600; letter-spacing: 0.5px;
    color: var(--green-deep); line-height: 1.1;
  }
  .person__role { font-size: 18px; color: var(--ink); margin-top: 6px; }
  .contact { margin-top: 26px; font-size: 19px; color: var(--ink-soft); line-height: 1.45; }
  .contact__label { color: var(--green-deep); font-weight: 700; }

  .brand {
    font-weight: 700; color: var(--ink);
    text-transform: uppercase; letter-spacing: 1px; line-height: 1.05;
  }
  .front__brand { position: absolute; right: 38px; top: 258px; text-align: right; }
  .front__brand .brand { font-size: 34px; }
  .tagline { font-size: 12px; color: var(--ink-muted); margin-top: 6px; }

  /* back */
  .back__brand {
    position: absolute; left: 0; right: 0; top: 38px;
    display: flex; justify-content: center; align-items: center; gap: 18px;
  }
  .back__brand .dot {
    width: 46px; height: 46px; border-radius: 50%;
    background: radial-gradient(circle at 35% 35%, var(--green-soft), var(--green-bright));
  }
  .back__brand .brand { font-size: 32px; }
  .back__brand .tagline { text-align: right; margin-top: 5px; }
  .pitch { position: absolute; left: 0; right: 0; top: 224px; text-align: center; }
  .pitch__heading { font-size: 20px; font-weight: 600; color: var(--green-deep); letter-spacing: 0.3px; }
  .pitch__list {
    list-style: none; font-style: italic; font-size: 18px;
    color: var(--ink-soft); line-height: 1.38; margin-top: 4px;
  }
  .bullet { color: var(--green-bright); font-style: normal; padding: 0 4px; }
  .pitch__offer {
    margin-top: 12px; font-size: 25px; font-weight: 700; font-style: italic;
    color: var(--green-bright);
  }
</style>
</head>
<body>
  <section class="card card--front" aria-label="Business card front">
    <div class="front__band"></div>
    <div class="front__mark"></div>
    <div class="front__accent"></div>
    <div class="front__details">
      <p class="person__name">DANIEL R. HAYES</p>
      <p class="person__role">PERSONAL FINANCIAL COACH</p>
      <div class="contact">
        <p><span class="contact__label">Mobile:</span> (555) 014-2290</p>
        <p>daniel@clearpathmoney.com</p>
        <p>www.clearpathmoney.com</p>
      </div>
    </div>
    <div class="front__brand">
      <p class="brand">Clearpath<br>Money Coaching</p>
      <p class="tagline">Achieve a new level of personal freedom</p>
    </div>
  </section>

  <section class="card card--back" aria-label="Business card back">
    <div class="back__brand">
      <span class="dot"></span>
      <div>
        <p class="brand">Clearpath<br>Money Coaching</p>
        <p class="tagline">Achieve a new level of personal freedom</p>
      </div>
    </div>
    <div class="pitch">
      <p class="pitch__heading">STRUGGLING WITH YOUR FINANCES?</p>
      <ul class="pitch__list">
        <li>Learn to become debt free <span class="bullet">●</span> Discover the power of cash</li>
        <li>Control your money instead of it controlling you</li>
        <li>Let us help you achieve a new level of financial freedom!</li>
      </ul>
      <p class="pitch__offer">SPECIAL OFFER!: FREE 30 minute consultation</p>
    </div>
  </section>
</body>
</html>
```